Quiet Harbor Podcast W/ Dr. Lena Marsh

Podcast Cover Art. I am in search of a re-design for my existing podcast. We have over 100 episodes, but I want to change the name to Quiet Harbor Podcast With Dr. Lena Marsh. I'm open to any ideas, and have attached source file image to use. ( note: NO brain images please).

```html
<!DOCTYPE html>
<html lang="en">
<head>
<meta charset="utf-8">
<title>Quiet Harbor Podcast With Dr. Lena Marsh</title>
<link rel="stylesheet" href="https://fonts.googleapis.com/css2?family=Poppins:wght@500;600;700&display=swap">
<style>
  :root {
    --bg-deep: #2e1d0a;
    --bg-mid: #3d2810;
    --swirl: rgba(160, 130, 90, 0.18);
    --title-white: #ffffff;
    --title-coral: #ff6b4f;
    --gold: #c4964f;
    --badge-gold: rgba(196, 150, 79, 0.72);
    --portrait-warm: #a8773f;
    --portrait-skin: #e9b99c;
    --portrait-coral: #ef5e3e;
  }
  * { margin: 0; padding: 0; box-sizing: border-box; }
  html, body { width: 1200px; height: 1200px; overflow: hidden; }
  body { font-family: "Poppins", Arial, sans-serif; }

  .cover {
    position: relative;
    width: 1200px;
    height: 1200px;
    overflow: hidden;
    background:
      radial-gradient(ellipse 420px 300px at 1050px 220px, var(--swirl), transparent 70%),
      radial-gradient(ellipse 360px 420px at 60px 820px, var(--swirl), transparent 70%),
      radial-gradient(ellipse 300px 220px at 220px 1140px, rgba(160,130,90,0.22), transparent 70%),
      linear-gradient(160deg, var(--bg-mid) 0%, var(--bg-deep) 60%, #2a1a08 100%);
  }

  .host-portrait {
    position: absolute;
    left: 660px;
    top: 450px;
    width: 540px;
    height: 750px;
    border-top-left-radius: 40px;
    background: linear-gradient(180deg,
      var(--portrait-warm) 0%,
      var(--portrait-skin) 30%,
      var(--portrait-skin) 55%,
      var(--portrait-coral) 78%,
      var(--portrait-coral) 100%);
    opacity: 0.9;
  }

  .title {
    position: absolute;
    left: 92px;
    top: 92px;
    font-weight: 700;
    font-size: 190px;
    line-height: 156px;
    letter-spacing: -2px;
  }
  .title-line { display: block; }
  .title-line--white { color: var(--title-white); }
  .title-line--coral { color: var(--title-coral); margin-left: 32px; }

  .host {
    position: absolute;
    left: 96px;
    top: 708px;
  }
  .host-with {
    display: block;
    color: var(--gold);
    font-weight: 600;
    font-size: 56px;
    line-height: 64px;
  }
  .host-name {
    display: block;
    color: var(--title-white);
    font-weight: 700;
    font-size: 72px;
    line-height: 84px;
    letter-spacing: -1px;
  }

  .badge {
    position: absolute;
    left: 96px;
    top: 1037px;
    width: 296px;
    height: 60px;
    background: var(--badge-gold);
    color: var(--title-white);
    font-weight: 500;
    font-size: 27px;
    letter-spacing: 12px;
    display: flex;
    align-items: center;
    justify-content: center;
    padding-left: 12px;
  }
</style>
</head>
<body>
  <main class="cover">
    <div class="host-portrait" role="img" aria-label="Illustrated portrait of the host in a coral checked blazer and light checked shirt"></div>

    <h1 class="title">
      <span class="title-line title-line--white">Quiet</span>
      <span class="title-line title-line--coral">Harbor</span>
    </h1>

    <p class="host">
      <span class="host-with">With</span>
      <span class="host-name">Dr. Lena Marsh</span>
    </p>

    <div class="badge">PODCAST</div>
  </main>
</body>
</html>
```